Mindfulness School for Children -- Business Cards

We're looking for business cards for our school directors and owners. We're a mindfulness school for children called little lanterns. Attached are our logos/icons.

```html
<!DOCTYPE html>
<html lang="en">
<head>
<meta charset="utf-8">
<title>little lanterns — Business Card</title>
<link rel="stylesheet" href="https://fonts.googleapis.com/css2?family=Raleway:wght@500;600&family=Arimo:wght@400&display=swap">
<style>
  :root {
    --bg: #2a2a2b;
    --card: #1c1d1f;
    --green: #7fcf9e;
    --aqua: #5fc4d8;
    --teal-chip: #7cc4b4;
    --accent: #6cc3c0;
    --text: #e9eaea;
    --rule: #5d5f62;
  }
  * { margin: 0; padding: 0; box-sizing: border-box; }
  html, body { width: 1200px; height: 1108px; overflow: hidden; }
  body {
    background: var(--bg);
    display: flex;
    align-items: center;
    justify-content: center;
    gap: 70px;
    font-family: "Arimo", Arial, sans-serif;
  }
  .card {
    width: 400px;
    height: 620px;
    border-radius: 22px;
    background: var(--card);
    box-shadow: 0 18px 40px rgba(0,0,0,.45);
    position: relative;
    overflow: hidden;
  }
  .card-front {
    display: flex;
    flex-direction: column;
    align-items: center;
    text-align: center;
    color: var(--text);
  }
  .brand {
    margin-top: 150px;
    display: flex;
    align-items: center;
    gap: 12px;
    font-family: "Raleway", sans-serif;
    font-weight: 500;
    font-size: 40px;
    letter-spacing: .5px;
    color: var(--aqua);
  }
  .brand-dot {
    width: 14px; height: 14px; border-radius: 50%;
    background: var(--aqua);
  }
  .person-name {
    margin-top: 105px;
    font-family: "Raleway", sans-serif;
    font-weight: 600;
    font-size: 30px;
    background: linear-gradient(90deg, var(--green), var(--aqua));
    -webkit-background-clip: text;
    background-clip: text;
    color: transparent;
  }
  .person-title { font-size: 17px; margin-top: 2px; }
  .icon-row {
    margin-top: 14px;
    width: 290px;
    display: flex;
    align-items: center;
    gap: 8px;
  }
  .icon-row .rule { flex: 1; height: 1px; background: var(--rule); }
  .icon-chip {
    width: 28px; height: 28px; border-radius: 4px;
    background: var(--teal-chip);
    display: flex; align-items: center; justify-content: center;
  }
  .contact { margin-top: 10px; font-size: 18px; line-height: 27px; }
  .divider { width: 290px; height: 1px; background: var(--rule); margin: 12px 0 10px; }
  .address { font-size: 18px; line-height: 27px; }
  .card-back .pattern {
    position: absolute; inset: 0;
    background: linear-gradient(45deg, #0b0b0c 0%, #1a1b1c 45%, #5a5b5d 100%);
  }
  .card-back .accent-dot {
    position: absolute;
    left: 218px; top: 440px;
    width: 54px; height: 54px; border-radius: 50%;
    background: var(--accent);
  }
</style>
</head>
<body>
  <section class="card card-front">
    <div class="brand"><span>little lanterns</span><span class="brand-dot"></span></div>
    <div class="person-name">Daniel Morrow</div>
    <div class="person-title">Managing Director</div>
    <div class="icon-row">
      <span class="rule"></span>
      <span class="icon-chip" aria-label="phone">
        <svg width="18" height="18" viewBox="0 0 24 24"><path fill="#1c1d1f" d="M6.6 10.8a15 15 0 0 0 6.6 6.6l2.2-2.2c.3-.3.7-.4 1-.2 1.1.4 2.3.6 3.6.6.6 0 1 .4 1 1V20c0 .6-.4 1-1 1A17 17 0 0 1 3 4c0-.6.4-1 1-1h3.5c.6 0 1 .4 1 1 0 1.3.2 2.5.6 3.6.1.3 0 .7-.2 1z"/></svg>
      </span>
      <span class="icon-chip" aria-label="email">
        <svg width="18" height="18" viewBox="0 0 24 24"><rect x="3" y="6" width="18" height="12" fill="none" stroke="#1c1d1f" stroke-width="2"/><path d="M3 6l9 7 9-7M3 18l7-6M21 18l-7-6" fill="none" stroke="#1c1d1f" stroke-width="1.6"/></svg>
      </span>
      <span class="icon-chip" aria-label="website">
        <svg width="18" height="18" viewBox="0 0 24 24"><circle cx="12" cy="12" r="9" fill="none" stroke="#1c1d1f" stroke-width="2"/><path d="M3 12h18M12 3c3 3 3 15 0 18M12 3c-3 3-3 15 0 18" fill="none" stroke="#1c1d1f" stroke-width="1.5"/></svg>
      </span>
      <span class="rule"></span>
    </div>
    <div class="contact">
      <div>055-210 384 617</div>
      <div>hello@littlelanterns.org</div>
      <div>www.littlelanterns.org</div>
    </div>
    <div class="divider"></div>
    <div class="address">
      <div>18, Willow Lane</div>
      <div>30219,Fairhaven</div>
    </div>
  </section>

  <section class="card card-back">
    <div class="pattern" role="img" aria-label="Repeating pattern of round brand emblems in glossy black fading to grey"></div>
    <span class="accent-dot" aria-hidden="true"></span>
  </section>
</body>
</html>
```